first fantastic look and impression

We are looking for a concept for letterhead, business card, emailfooter and template for invoices or offers for our company in the consultation business.
The dancer is a symbol who we are: it looks simple, but there is a lot of hard work and many years of training in this movement. The look is also what we want: elegant, modern, strong, with a touch of extravaganza
Target Market(s)
Hotelbusiness , Consulting
Font styles to use
Sans Serif
Other font styles liked:
- please give us a option we are open
Requirements
Must have
- We are not typical consultants but sparring partners and coaches for the hotel and that should also be expressed in the design. Maybe there is an icon that supports the whole thing. We are more modern and bolder than our industry colleagues.
we are modern, fresh, agile, fast
Nice to have
- a icon

```html
<!DOCTYPE html>
<html lang="en">
<head>
<meta charset="utf-8">
<title>Lindqvist+Partner – Business Card</title>
<link rel="stylesheet" href="https://fonts.googleapis.com/css2?family=Montserrat:wght@400;500;700&display=swap">
<style>
  :root {
    --stage: #141414;
    --card: #0b0d0d;
    --ink: #f2f2f2;
    --ink-soft: #d9d9d9;
    --rule: #e6e6e6;
  }
  * { margin: 0; padding: 0; box-sizing: border-box; }
  html, body {
    width: 1200px; height: 900px; overflow: hidden;
    background: var(--stage);
    font-family: "Montserrat", sans-serif;
  }
  .card {
    position: absolute; left: 120px; top: 176px;
    width: 960px; height: 548px;
    background: linear-gradient(135deg, #0a0b0b 0%, #101414 60%, #0c0f0f 100%);
    box-shadow: 0 24px 60px rgba(0,0,0,.6);
  }
  .card__frame {
    position: absolute; left: 44px; top: 44px; right: 44px; bottom: 44px;
    border: 2px solid var(--rule);
  }
  .card__wordmark {
    position: absolute; left: 96px; bottom: 33px;
    padding: 0 16px;
    background: #0c0f0f;
    color: var(--ink-soft);
    font-size: 18px; font-weight: 500; letter-spacing: 4px;
    text-transform: uppercase; line-height: 22px;
  }
  .brand {
    position: absolute; left: 96px; top: 190px; width: 330px;
    display: flex; align-items: center; gap: 16px;
    color: var(--ink);
    font-size: 30px; font-weight: 500; letter-spacing: 1px;
  }
  .brand__square { width: 18px; height: 18px; background: var(--ink); flex: none; }
  .card__divider {
    position: absolute; left: 462px; top: 150px;
    width: 2px; height: 210px; background: var(--rule);
  }
  .contact {
    position: absolute; left: 500px; top: 168px; color: var(--ink);
  }
  .contact__name { font-size: 27px; font-weight: 700; letter-spacing: .5px; text-transform: uppercase; }
  .contact__role { font-size: 22px; font-weight: 500; margin-bottom: 20px; }
  .contact__list { list-style: none; font-size: 21px; font-weight: 400; line-height: 32px; }
  .contact__item { display: flex; align-items: center; gap: 12px; }
  .contact__icon { width: 20px; height: 20px; flex: none; fill: none; stroke: var(--ink); stroke-width: 2; }
  .contact__icon--solid { fill: var(--ink); stroke: none; }
</style>
</head>
<body>
  <main class="card">
    <div class="card__frame"></div>
    <div class="card__wordmark">Lindqvist+Partner</div>

    <div class="brand"><span class="brand__square"></span>Lindqvist+Partner</div>

    <div class="card__divider"></div>

    <section class="contact">
      <h1 class="contact__name">Elias Brandner</h1>
      <p class="contact__role">Managing Director</p>
      <ul class="contact__list">
        <li class="contact__item">
          <svg class="contact__icon contact__icon--solid" viewBox="0 0 24 24"><path d="M6.6 10.8a15.2 15.2 0 0 0 6.6 6.6l2.2-2.2a1 1 0 0 1 1-.25 11.4 11.4 0 0 0 3.6.57 1 1 0 0 1 1 1V20a1 1 0 0 1-1 1A17 17 0 0 1 3 4a1 1 0 0 1 1-1h3.5a1 1 0 0 1 1 1c0 1.25.2 2.45.57 3.57a1 1 0 0 1-.25 1z"/></svg>
          +43555010240
        </li>
        <li class="contact__item">
          <svg class="contact__icon" viewBox="0 0 24 24"><rect x="3" y="5" width="18" height="14"/><path d="M3 5l9 8 9-8"/></svg>
          info@lindqvistpartner.com
        </li>
        <li class="contact__item">
          <svg class="contact__icon" viewBox="0 0 24 24"><circle cx="12" cy="12" r="9"/><path d="M3 12h18M12 3c3 3 3 15 0 18M12 3c-3 3-3 15 0 18"/></svg>
          www.lindqvistpartner.com
        </li>
        <li class="contact__item">
          <svg class="contact__icon contact__icon--solid" viewBox="0 0 24 24"><path d="M12 2a7 7 0 0 0-7 7c0 5 7 13 7 13s7-8 7-13a7 7 0 0 0-7-7zm0 9.5A2.5 2.5 0 1 1 12 6.5a2.5 2.5 0 0 1 0 5z"/></svg>
          Bergtal/Austria
        </li>
      </ul>
    </section>
  </main>
</body>
</html>
```